Fresh, modern, fun business card for pediatric dental practice

Need a business card for fresh, modern, fun pediatric dental practice

Clean look that matches our website's font and colors

We prefer the look of curved corners on business cards

Target Market(s)

parents (mothers) of young children, professionals, mid-high class

Industry/Entity Type

Dental

Contact Information for Business Card

Maplebrook Pediatric Dentistry
482 Quarry Lane
Suite 517
Fernhollow, PA 17590
717.555.0193
www.maplebrookkidsdental.example

Mei-Ran Tsai, DMD
Corinne Walbeck, DMD
(we are working on our email address, but we would like that on the card as well)

Font styles to use
Sans Serif

Requirements
Must have
• All info; we would also like to make cards for individual staff members
• colors from our website and color palatte, attatched
• use same font and design as website for branding
Nice to have
• clean, simple card that has a pop of color
• we would like to see a few designs with our tag line "where smiles get brighter"
• we are not sure if we want to have it on there or not
• we would like to see a few designs incorporating the ribbon graphic on our website where the word WELCOME is

```html
<!DOCTYPE html>
<html lang="en">
<head>
<meta charset="utf-8">
<title>Maplebrook Pediatric Dentistry – Business Card</title>
<link href="https://fonts.googleapis.com/css2?family=Open+Sans:wght@700&family=Work+Sans:wght@400;600&display=swap" rel="stylesheet">
<style>
  :root {
    --page: #e7e4e1;
    --card: #1d1d1d;
    --sun: #f6b21c;
    --text: #f2f2f2;
  }
  * { box-sizing: border-box; margin: 0; padding: 0; }
  html, body { width: 1200px; height: 715px; overflow: hidden; }
  body {
    background: var(--page);
    font-family: "Work Sans", Arial, sans-serif;
    position: relative;
  }
  .card {
    position: absolute;
    top: 212px;
    width: 500px;
    height: 290px;
    background: var(--card);
    border-radius: 18px;
    box-shadow: 0 10px 28px rgba(0,0,0,.25);
    overflow: hidden;
  }
  .card--front { left: 60px; }
  .card--back { left: 640px; }

  .brand {
    font-family: "Open Sans", Arial, sans-serif;
    font-weight: 700;
    color: var(--sun);
    line-height: 1;
  }
  .card--front .brand {
    position: absolute;
    left: 0; right: 0; top: 100px;
    text-align: center;
  }
  .card--front .brand__name { font-size: 50px; letter-spacing: 1px; }
  .card--front .brand__line { font-size: 19px; letter-spacing: 3px; margin-top: 8px; }

  .card--back .brand {
    position: absolute;
    left: 36px; top: 30px;
  }
  .card--back .brand__name { font-size: 34px; letter-spacing: .5px; }
  .card--back .brand__line { font-size: 13px; letter-spacing: 2px; margin-top: 5px; }

  .person {
    position: absolute;
    left: 36px; top: 122px;
  }
  .person__name {
    font-weight: 600;
    color: var(--sun);
    font-size: 16px;
    letter-spacing: .8px;
    text-transform: uppercase;
  }
  .person__title { color: var(--text); font-size: 10px; margin-top: 2px; }

  .contact {
    position: absolute;
    left: 36px; top: 176px;
    list-style: none;
    color: var(--text);
    font-size: 11px;
    line-height: 16px;
  }
  .contact li { display: flex; align-items: center; gap: 6px; }
  .contact .icon { width: 9px; height: 9px; flex: none; }
  .contact .spacer { width: 9px; flex: none; }

  .sun-disc {
    position: absolute;
    right: 40px; top: 90px;
    width: 150px; height: 150px;
  }
</style>
</head>
<body>

<section class="card card--front" aria-label="Card front">
  <div class="brand">
    <div class="brand__name">maplebrook</div>
    <div class="brand__line">pediatric dentistry</div>
  </div>
</section>

<section class="card card--back" aria-label="Card back">
  <div class="brand">
    <div class="brand__name">maplebrook</div>
    <div class="brand__line">pediatric dentistry</div>
  </div>

  <div class="person">
    <div class="person__name">Corinne Walbeck</div>
    <div class="person__title">DMD</div>
  </div>

  <ul class="contact">
    <li><span class="spacer"></span>482 Quarry Lane</li>
    <li><span class="spacer"></span>Suite 517 Fernhollow, PA 17590</li>
    <li>
      <svg class="icon" viewBox="0 0 10 10" aria-hidden="true"><path d="M2 1 L3.5 1 L4.2 3 L3.2 3.8 Q4.2 5.8 6.2 6.8 L7 5.8 L9 6.5 L9 8 Q9 9 8 9 Q1 8.5 1 2 Q1 1 2 1 Z" fill="var(--sun)"/></svg>
      717.555.0193
    </li>
    <li>
      <svg class="icon" viewBox="0 0 10 10" aria-hidden="true"><rect x="0.8" y="2" width="8.4" height="6" fill="none" stroke="var(--sun)" stroke-width="1"/><path d="M1 2.3 L5 5.4 L9 2.3" fill="none" stroke="var(--sun)" stroke-width="1"/></svg>
      hello@maplebrookkidsdental.example
    </li>
    <li>
      <svg class="icon" viewBox="0 0 10 10" aria-hidden="true"><circle cx="5" cy="5" r="4" fill="none" stroke="var(--sun)" stroke-width="1"/><path d="M1 5 H9 M5 1 Q2.5 5 5 9 M5 1 Q7.5 5 5 9" fill="none" stroke="var(--sun)" stroke-width=".8"/></svg>
      www.maplebrookkidsdental.example
    </li>
  </ul>

  <svg class="sun-disc" viewBox="0 0 150 150" aria-hidden="true">
    <circle cx="75" cy="75" r="60" fill="var(--sun)"/>
  </svg>
</section>

</body>
</html>
```